BRIGHTWATER RV Resort needs a logo and advertising poster

We need an advertising poster for our epic RV Resort located on north end of Tillon Lake, (Northern Saskatchewan, trees no mountains)
SEASONAL FULL SERVICE SITES with marina and lake access.
Sauna/plunge, disc golf , hiking/quad trails, and pet friendly.
We are after a fun 70,s themed simple poster. Please use brand guide for colours and redo logo to be Brightwater Resort.

Target Market(s)

RV owners looking for permeant sites. No tenting.

Font styles to use
Other font styles liked:
• See brand guide

Requirements
Must have
• Change exisiting branding to BRIGHTWATER RESORT instead of coffee Emphasis Limited sites.... Referral discount. Phone number.
Nice to have
• .
Should not have
• Keep it simple

```html
<!DOCTYPE html>
<html lang="en">
<head>
<meta charset="utf-8">
<title>Tillon Lake – Brightwater Resort</title>
<link rel="stylesheet" href="https://fonts.googleapis.com/css2?family=Lobster&family=Bebas+Neue&family=Poppins:wght@600;700&display=swap">
<style>
  :root{
    --frame:#f3d99a;
    --paper:#f6f0e3;
    --green:#6b7f4e;
    --rose:#b8705c;
    --rose-soft:#d9a08c;
    --ink:#2a2c2c;
  }
  *{box-sizing:border-box;margin:0;padding:0}
  html,body{width:919px;height:1200px;overflow:hidden;background:var(--frame)}
  .poster{position:relative;width:919px;height:1200px;background:var(--frame);padding:14px}
  .poster__paper{
    position:relative;width:100%;height:100%;
    background:radial-gradient(ellipse at center,#f8f3e8 55%,#efe5cf 100%);
    overflow:hidden;
  }
  .title{
    position:absolute;left:0;right:0;top:32px;z-index:2;text-align:center;
    font-family:"Lobster",cursive;font-size:118px;line-height:1;font-weight:400;
    color:var(--green);
    text-shadow:4px -3px 0 var(--paper),7px -5px 0 var(--rose-soft);
  }
  .subtitle{
    position:absolute;left:20px;right:20px;top:162px;z-index:2;text-align:center;
    font-family:"Bebas Neue",sans-serif;font-size:48px;line-height:40px;
    letter-spacing:2.5px;color:var(--rose);
  }
  .scene{
    position:absolute;left:12px;top:252px;width:850px;height:660px;z-index:1;
    border-radius:48% 52% 40% 44% / 18% 22% 30% 34%;
    background:linear-gradient(180deg,#8fb3bd 0%,#5d8fa0 28%,#3d6b57 48%,#233833 58%,#4d7e8e 66%,#c8d3c2 82%,#e9dfc8 100%);
  }
  .offer{
    position:absolute;left:72px;top:922px;z-index:2;
    font-family:"Lobster",cursive;font-size:28px;font-weight:400;color:var(--green);
  }
  .features{position:absolute;left:62px;top:963px;display:flex;gap:7px;list-style:none;z-index:2}
  .feature{
    display:flex;align-items:flex-start;gap:6px;height:57px;padding:8px 8px 0 8px;
    border:1.5px solid var(--rose-soft);border-radius:10px;
    font-family:"Poppins",sans-serif;font-weight:600;font-size:14.5px;line-height:18px;color:var(--ink);
  }
  .feature svg{flex:none;margin-top:2px}
  .badge{position:absolute;left:676px;top:886px;width:160px;height:160px;z-index:2}
  .badge__text{
    position:absolute;inset:0;display:flex;flex-direction:column;align-items:center;justify-content:center;
    font-family:"Poppins",sans-serif;font-weight:700;color:var(--paper);text-align:center;line-height:1;
  }
  .badge__small{font-size:13px;line-height:13px}
  .badge__big{font-size:40px;margin:4px 0 2px}
  .footer{position:absolute;left:72px;top:1050px;display:flex;align-items:center;gap:16px;z-index:2}
  .brand{
    display:flex;align-items:center;gap:8px;width:128px;
    font-family:"Bebas Neue",sans-serif;font-size:26px;line-height:1;color:var(--green);
  }
  .brand__mark{width:14px;height:14px;background:var(--green);flex:none}
  .contact{display:flex;align-items:center;gap:6px;font-family:"Bebas Neue",sans-serif;font-size:37px;line-height:1;color:var(--ink)}
  .contact svg{flex:none}
</style>
</head>
<body>
<main class="poster">
  <div class="poster__paper">
    <h1 class="title">Tillon Lake</h1>
    <p class="subtitle">Northern Saskatchewan larger seasonal<br>sites and limited sites</p>

    <div class="scene" role="img" aria-label="Retro illustration of two kayakers paddling on a calm lake surrounded by pine forest, reflected in the water"></div>

    <p class="offer">We provide seasonal full service site with</p>
    <ul class="features">
      <li class="feature" style="width:142px"><svg width="16" height="14" viewBox="0 0 16 14"><path d="M2 7l4 4 8-9" fill="none" stroke="var(--rose)" stroke-width="2.6" stroke-linecap="round"/></svg><span>Marina and<br>lake access</span></li>
      <li class="feature" style="width:109px"><svg width="16" height="14" viewBox="0 0 16 14"><path d="M2 7l4 4 8-9" fill="none" stroke="var(--rose)" stroke-width="2.6" stroke-linecap="round"/></svg><span>Sauna/<br>plunge</span></li>
      <li class="feature" style="width:81px"><svg width="16" height="14" viewBox="0 0 16 14"><path d="M2 7l4 4 8-9" fill="none" stroke="var(--rose)" stroke-width="2.6" stroke-linecap="round"/></svg><span>Disc<br>golf</span></li>
      <li class="feature" style="width:126px"><svg width="16" height="14" viewBox="0 0 16 14"><path d="M2 7l4 4 8-9" fill="none" stroke="var(--rose)" stroke-width="2.6" stroke-linecap="round"/></svg><span>Hiking/<br>quad trails</span></li>
      <li class="feature" style="width:112px"><svg width="16" height="14" viewBox="0 0 16 14"><path d="M2 7l4 4 8-9" fill="none" stroke="var(--rose)" stroke-width="2.6" stroke-linecap="round"/></svg><span>&nbsp;Pet<br>&nbsp;friendly</span></li>
    </ul>

    <div class="badge">
      <svg width="160" height="160" viewBox="0 0 160 160">
        <circle cx="80" cy="80" r="70" fill="var(--rose)"/>
        <circle cx="80" cy="80" r="74" fill="none" stroke="var(--rose)" stroke-width="8" stroke-dasharray="5 4"/>
      </svg>
      <div class="badge__text">
        <span class="badge__small">LIMITED<br>SITES</span>
        <span class="badge__big">5%</span>
        <span class="badge__small">REFERRAL<br>DISCOUNT</span>
      </div>
    </div>

    <footer class="footer">
      <div class="brand"><span class="brand__mark"></span><span>BRIGHTWATER<br>RESORT</span></div>
      <div class="contact">
        <svg width="18" height="18" viewBox="0 0 24 24"><path d="M6.6 10.8a15 15 0 006.6 6.6l2.2-2.2a1 1 0 011-.25 11 11 0 003.6.6 1 1 0 011 1V20a1 1 0 01-1 1A17 17 0 013 4a1 1 0 011-1h3.5a1 1 0 011 1 11 11 0 00.6 3.6 1 1 0 01-.25 1z" fill="var(--rose)"/></svg>
        <span>1-306-555-0148</span>
      </div>
      <div class="contact">
        <svg width="22" height="22" viewBox="0 0 24 24" fill="none" stroke="var(--rose)" stroke-width="2"><circle cx="12" cy="12" r="9"/><path d="M3 12h18M12 3c3 3 3 15 0 18M12 3c-3 3-3 15 0 18"/></svg>
        <span>WWW.BRIGHTWATERRESORT.COM</span>
      </div>
    </footer>
  </div>
</main>
</body>
</html>
```